full stationary design for a modern sleek design company

we are a design company that does modern minimalistic interior design works as well as other design services for high end clients.
we need a full stationary design including and not limited to (double sided business card, letter head, envelopes, documents folder...etc) that reflects the modern style design we do.
sleek modern and minimalistic is the requirements.
Updates

please use the latest attached files as there was a slight modification on the logo Added Wednesday, March 1, 2017

minor update on the logo files in JPG and PSD has been updated kindly follow the new attachments. Added Thursday, March 2, 2017

Target Market(s)

modern minimalist clients

Industry/Entity Type

Design Agency

Requirements
Must have
• the logo
Nice to have
• i like the colors in the colored 3D logo attached
Should not have
• too many colors

```html
<!DOCTYPE html>
<html lang="en">
<head>
<meta charset="utf-8">
<title>Linea Atelier — Business Card</title>
<link rel="stylesheet" href="https://fonts.googleapis.com/css2?family=Source+Sans+3:wght@400;600&display=swap">
<style>
  :root {
    --backdrop: #e9e6e2;
    --card-light: #ffffff;
    --card-dark: #323435;
    --ink: #3a3b3c;
    --accent: #f39321;
    --rule: #d6d6d6;
    --white: #ffffff;
  }
  * { margin: 0; padding: 0; box-sizing: border-box; }
  html, body {
    width: 1200px; height: 987px; overflow: hidden;
    background: var(--backdrop);
    font-family: "Source Sans 3", sans-serif;
  }
  .sheet { position: relative; width: 1200px; height: 987px; }
  .card {
    position: absolute; left: 293px; width: 615px; height: 351px;
  }
  .card--front { top: 130px; background: var(--card-light); }
  .card--back { top: 506px; background: var(--card-dark); }

  .brand {
    position: absolute; display: flex; align-items: center; gap: 10px;
    font-weight: 600; letter-spacing: 0.12em; text-transform: uppercase;
    white-space: nowrap;
  }
  .brand__mark { width: 14px; height: 14px; background: var(--accent); flex: none; }
  .card--front .brand { left: 48px; top: 161px; font-size: 23px; color: var(--ink); }
  .card--back .brand {
    left: 0; right: 0; top: 144px; justify-content: center;
    font-size: 36px; color: var(--white);
  }
  .card--back .brand__mark { width: 20px; height: 20px; }

  .divider {
    position: absolute; left: 334px; top: 72px; width: 1px; height: 208px;
    background: var(--rule);
  }
  .contact { position: absolute; left: 359px; top: 72px; color: var(--ink); }
  .contact__name {
    font-size: 22px; font-weight: 600; color: var(--accent);
    letter-spacing: 0.02em; line-height: 26px;
  }
  .contact__role { font-size: 16px; line-height: 20px; margin-bottom: 14px; }
  .contact__address { font-size: 16px; line-height: 22px; margin-bottom: 6px; }
  .contact__list { list-style: none; }
  .contact__item {
    display: flex; align-items: center; gap: 8px;
    font-size: 16px; line-height: 23.5px;
  }
  .contact__icon { width: 13px; height: 13px; flex: none; fill: var(--accent); }
</style>
</head>
<body>
<main class="sheet">
  <section class="card card--front">
    <div class="brand"><span class="brand__mark"></span>Linea Atelier</div>
    <div class="divider"></div>
    <div class="contact">
      <p class="contact__name">ADAM REYES</p>
      <p class="contact__role">CEO&amp;Founder</p>
      <p class="contact__address">214 Alder Court<br>Portland, Oregon 97205</p>
      <ul class="contact__list">
        <li class="contact__item">
          <svg class="contact__icon" viewBox="0 0 16 16"><path d="M3.5 1l2.5 3-1.5 2c1 2 3 4 5 5l2-1.5 3 2.5-1.5 2.5C8 15 1 8 1 2.5z"/></svg>
          (555) 210 4417
        </li>
        <li class="contact__item">
          <svg class="contact__icon" viewBox="0 0 16 16"><path d="M4 0h8a1 1 0 0 1 1 1v14a1 1 0 0 1-1 1H4a1 1 0 0 1-1-1V1a1 1 0 0 1 1-1zm1 2v10h6V2zm3 11a1 1 0 1 0 0 2 1 1 0 0 0 0-2z"/></svg>
          (555) 382 0956
        </li>
        <li class="contact__item">
          <svg class="contact__icon" viewBox="0 0 16 16"><path d="M0 3h16v10H0zm1.5 1.3V12h13V4.3L8 9z"/></svg>
          adam@lineaatelier.com
        </li>
        <li class="contact__item">
          <svg class="contact__icon" viewBox="0 0 16 16"><circle cx="8" cy="8" r="8"/><path d="M4 5c2 0 3 1 2.5 3S4 9 5 12M10 2c0 2 2 2 1 4s1 3 3 3" stroke="#fff" stroke-width="1.3" fill="none"/></svg>
          www.lineaatelier.com
        </li>
      </ul>
    </div>
  </section>

  <section class="card card--back">
    <div class="brand"><span class="brand__mark"></span>Linea Atelier</div>
  </section>
</main>
</body>
</html>
```